Design 4 pages for an event discovery website

This is a contest for the design of 4 pages for an events discovery website. The feature is part of the new sign-up process.

Please see the attached document for a full scope, mockups and the parent category icons.

Target Market(s)

18-35 Australian event goers

Industry/Entity Type

Events

Number of Pages Required

4 page

```html
<!DOCTYPE html>
<html lang="en">
<head>
<meta charset="utf-8">
<title>Stagely – Sign up, step 1 of 5</title>
<link rel="stylesheet" href="https://fonts.googleapis.com/css2?family=Open+Sans:wght@400;600&display=swap">
<style>
  :root {
    --brand: #67c5d5;
    --brand-dark: #3fb4d8;
    --ink: #ffffff;
    --panel: rgba(10, 10, 10, 0.82);
    --footer: #1b1b1b;
    --footer-text: #a8a8a8;
    --button-face: #ececec;
    --button-text: #3a3a3a;
    --muted-step: #4a4a4a;
    --chirp: #2aa8e6;
    --snap: #8a6a55;
    --tune: #79b84a;
    --vault: #444444;
  }
  * { box-sizing: border-box; margin: 0; padding: 0; }
  html, body { width: 1200px; height: 788px; overflow: hidden; }
  body { font-family: "Open Sans", Arial, sans-serif; background: #0d1a22; position: relative; }

  .site-header { position: absolute; left: 0; top: 0; width: 1200px; height: 82px; background: var(--brand); }
  .brand { position: absolute; left: 118px; top: 14px; display: flex; align-items: baseline; gap: 10px; color: var(--ink); }
  .brand-name { font-size: 44px; font-weight: 600; letter-spacing: -1px; }
  .brand-tagline { font-size: 15px; font-weight: 400; }
  .search { position: absolute; left: 697px; top: 21px; width: 208px; height: 39px; background: #fff; border-radius: 3px; display: flex; align-items: center; padding: 0 12px 0 15px; }
  .search-label { flex: 1; font-size: 13px; color: #9a9a9a; }
  .header-button { position: absolute; top: 21px; height: 39px; border-radius: 3px; background: linear-gradient(#fff, #e4e4e4); color: #9a9a9a; font-size: 16px; display: flex; align-items: center; justify-content: center; box-shadow: 0 1px 2px rgba(0,0,0,.15); }
  .signup { left: 912px; width: 81px; }
  .login { left: 1000px; width: 81px; }

  .hero { position: absolute; left: 0; top: 82px; width: 1200px; height: 624px;
    background: radial-gradient(ellipse at 50% 85%, #4f7f92 0%, #2a4c5c 30%, #122430 60%, #070b0f 100%); }

  .step-title { position: absolute; left: 120px; top: 164px; display: flex; align-items: center; color: var(--ink); }
  .step-word { font-size: 40px; font-weight: 600; margin-right: 10px; }
  .step-badge { width: 44px; height: 44px; border-radius: 50%; display: flex; align-items: center; justify-content: center; font-size: 20px; }
  .step-current { background: var(--brand); }
  .step-total { background: var(--muted-step); }
  .step-of { font-size: 14px; margin: 0 8px; }

  .link-panel { position: absolute; left: 121px; top: 230px; width: 960px; height: 234px; background: var(--panel); }
  .link-intro { position: absolute; left: 31px; top: 36px; width: 880px; font-size: 15px; line-height: 25px; color: var(--ink); }
  .account { position: absolute; top: 117px; width: 174px; }
  .account-button { display: flex; height: 39px; background: var(--button-face); border-radius: 3px; overflow: hidden; }
  .account-icon { width: 37px; height: 39px; position: relative; }
  .account-icon::after { content: ""; position: absolute; right: -6px; top: 14px; border-left: 6px solid; border-left-color: inherit; border-top: 6px solid transparent; border-bottom: 6px solid transparent; }
  .account-icon .dot { position: absolute; left: 12px; top: 13px; width: 13px; height: 13px; border-radius: 2px; background: rgba(255,255,255,.85); }
  .account-name { flex: 1; padding-left: 18px; font-size: 18px; font-weight: 600; color: var(--button-text); line-height: 39px; }
  .account-note { margin-top: 9px; font-size: 11px; line-height: 15px; color: #bdbdbd; padding-left: 3px; }
  .account-note.linked { color: var(--brand-dark); }
  .chirp { left: 31px; } .chirp .account-icon { background: var(--chirp); border-color: var(--chirp); }
  .snap { left: 271px; } .snap .account-icon { background: var(--snap); border-color: var(--snap); }
  .tune { left: 510px; } .tune .account-icon { background: var(--tune); border-color: var(--tune); }
  .vault { left: 750px; } .vault .account-icon { background: var(--vault); border-color: var(--vault); }

  .site-footer { position: absolute; left: 0; top: 706px; width: 1200px; height: 82px; background: var(--footer); }
  .copyright { position: absolute; left: 119px; top: 31px; font-size: 13px; color: var(--footer-text); }
  .social-links { position: absolute; left: 761px; top: 24px; display: flex; gap: 9px; list-style: none; }
  .social-links li { width: 33px; height: 33px; border-radius: 50%; }
</style>
</head>
<body>
  <header class="site-header">
    <div class="brand"><span class="brand-name">Stagely</span><span class="brand-tagline">Find Events</span></div>
    <div class="search">
      <span class="search-label">Search</span>
      <svg width="18" height="18" viewBox="0 0 18 18" aria-hidden="true"><circle cx="7.5" cy="7.5" r="5.5" fill="none" stroke="#9a9a9a" stroke-width="2.2"/><line x1="11.5" y1="11.5" x2="16" y2="16" stroke="#9a9a9a" stroke-width="2.6" stroke-linecap="round"/></svg>
    </div>
    <a class="header-button signup">Signup</a>
    <a class="header-button login">Login</a>
  </header>

  <main class="hero" role="img" aria-label="Concert stage with lighting rig and spotlight beams in blue haze"></main>

  <h1 class="step-title">
    <span class="step-word">Step</span>
    <span class="step-badge step-current">1</span>
    <span class="step-of">of</span>
    <span class="step-badge step-total">5</span>
  </h1>

  <section class="link-panel">
    <p class="link-intro">Link in all your other social media accounts and music players By linking your accounts, we can save you a lot of time by automatically determining your interests</p>
    <div class="account chirp">
      <div class="account-button"><span class="account-icon"><span class="dot"></span></span><span class="account-name">Chirpnet</span></div>
      <p class="account-note linked">Linked</p>
    </div>
    <div class="account snap">
      <div class="account-button"><span class="account-icon"><span class="dot"></span></span><span class="account-name">Snapgrid</span></div>
    </div>
    <div class="account tune">
      <div class="account-button"><span class="account-icon"><span class="dot"></span></span><span class="account-name">Tunestream</span></div>
      <p class="account-note">We don't have that feature yet<br>but have required your interest</p>
    </div>
    <div class="account vault">
      <div class="account-button"><span class="account-icon"><span class="dot"></span></span><span class="account-name">Songvault</span></div>
    </div>
  </section>

  <footer class="site-footer">
    <p class="copyright">Copyright &copy; 2015 Stagely. All rights reserved</p>
    <ul class="social-links">
      <li style="background:#3b5998"></li>
      <li style="background:#2aa8e6"></li>
      <li style="background:#3a3a3a"></li>
      <li style="background:#cb2027"></li>
      <li style="background:#f57d00"></li>
      <li style="background:#e52d27"></li>
      <li style="background:#517fa4"></li>
      <li style="background:#5aa03a"></li>
    </ul>
  </footer>
</body>
</html>
```